Web Design Project

Psychotherapy and Counselling Practice needs a landing page web design.

My business "Larkfield Advisory" specialises in the treatment of Anxiety and Depression with a holistic approach, endeavouring to unlock the key that holds us to ransom in a life that is imbalanced, frustrating, and ultimately of our own making due to our own perceptions and behaviours.

There is much that impacts us which we cannot change, but we are always in control of how we think, and how we frame our experiences.....learning to challenge those thoughts and behaviours that are destructive and disempowering opens up a world of joyful possibility. Life is about making choices, learn to make wiser and healthier choices.......

Larkfield Advisory has a client base of individual clients but will seek to expand to offer services to the Corporate world by offering an adjunct to employers for established "Wellness Programs".

Larkfield Advisory is a highly professional, ethically bound business, with the needs of the client at the forefront of all we do.

Larkfield Advisory wishes to avoid the usual "jargon driven" psychobabble offered on many counselling web pages. It aims to be stylishly presented, clean in look and with as few "words" as possible and a largely white background (faster loading and more powerful impact of what is stated), those words contained in the webpage should be meaningful, persuasive and have an impact simply at glance. Larkfield does not want , or expect, those prospective clients in need of support , to be reading through volumes of industry driven cliches.

At this point Larkfield is just looking for a high quality landing page. However in time this will likely expand to include other sections such as case studies, video content etc.

Target Market(s)

Those in need of emotional support, suffering mental health issues, and those simply wanting to become self aware supported by a mindful therapist.

Industry/Entity Type

Industry

Requirements
Must have
• The design must incorporate the Larkfield logo and colour schemes found on the attached files.

```html
<!DOCTYPE html>
<html lang="en">
<head>
<meta charset="utf-8">
<title>Larkfield Advisory</title>
<link rel="stylesheet" href="https://fonts.googleapis.com/css2?family=PT+Sans:wght@400;700&display=swap">
<style>
  :root {
    --green: #8aac12;
    --grey: #929292;
    --grey-dark: #6f6f6f;
    --band: #757575;
    --tile: #7a7a7a;
    --white: #ffffff;
  }
  * { margin: 0; padding: 0; box-sizing: border-box; }
  html, body { width: 1200px; height: 891px; overflow: hidden; background: var(--white); }
  body { font-family: "PT Sans", Tahoma, sans-serif; font-weight: 700; position: relative; }
  .page { position: relative; width: 1200px; height: 891px; }

  .site-header { position: relative; z-index: 2; }
  .brand-tile {
    position: absolute; left: 7px; top: 8px; width: 134px; height: 133px;
    background: var(--tile); border-radius: 6px;
    display: flex; align-items: center; justify-content: center;
  }
  .brand-tile span { color: var(--green); font-weight: 400; font-size: 20px; letter-spacing: 0.5px; }

  .main-nav { position: absolute; top: 82px; left: 661px; display: flex; gap: 30px; }
  .main-nav a { color: var(--green); text-decoration: none; font-size: 18px; letter-spacing: 0.3px; }

  .hero {
    position: absolute; left: 0; top: 130px; width: 1200px; height: 682px;
    background: linear-gradient(90deg, #ffffff 0%, #fdfdfd 50%, #f8f8f8 100%);
    overflow: hidden;
  }
  .hero-mark {
    position: absolute; left: 80px; top: 318px;
    color: var(--green); font-weight: 400; font-size: 84px; letter-spacing: 1px; line-height: 1;
  }
  .swoosh { position: absolute; left: 0; top: 568px; }

  .quote { position: absolute; left: 728px; top: 260px; color: var(--grey); }
  .quote p { font-size: 29px; line-height: 44px; }
  .quote p + p { padding-left: 17px; }
  .quote cite { display: block; font-style: normal; font-size: 16px; margin: 6px 0 0 26px; }

  .contact { position: absolute; left: 740px; top: 476px; color: var(--grey); }
  .tagline { font-size: 22px; }
  .tagline em { font-style: normal; color: var(--green); }
  .name { font-size: 22px; margin-top: 38px; }
  .creds { font-size: 16px; margin-top: 6px; }
  .lines { font-size: 16px; margin-top: 30px; line-height: 26px; }

  .site-footer { position: absolute; left: 0; top: 812px; width: 1200px; height: 79px; background: var(--white); }
  .copyright { position: absolute; left: 83px; top: 39px; font-size: 12px; color: var(--grey-dark); }
  .social { position: absolute; left: 432px; top: 23px; display: flex; gap: 11px; }
  .social span { width: 30px; height: 29px; background: var(--green); display: block; }
  .web { position: absolute; right: 72px; top: 33px; font-size: 17px; color: var(--grey-dark); }
  .web em { font-style: normal; color: var(--green); }
</style>
</head>
<body>
<div class="page">
  <header class="site-header">
    <div class="brand-tile"><span>LARKFIELD</span></div>
    <nav class="main-nav">
      <a href="#">HOME</a>
      <a href="#">ABOUT US</a>
      <a href="#">CASE STUDIES</a>
      <a href="#">VIDEO CONTENT</a>
    </nav>
  </header>

  <section class="hero">
    <div class="hero-mark">LARKFIELD</div>
    <svg class="swoosh" width="1200" height="114" viewBox="0 0 1200 114" aria-hidden="true">
      <path d="M0 50 Q 420 56 1200 24 L1200 114 L0 114 Z" fill="var(--band)"/>
      <path d="M0 8 Q 320 42 1085 12 Q 340 58 0 42 Z" fill="var(--green)"/>
    </svg>
  </section>

  <div class="quote">
    <p>“With the new day comes</p>
    <p>new strength new thoughts”</p>
    <cite>( Harriet Vale )</cite>
  </div>

  <div class="contact">
    <p class="tagline"><em>Consulting</em> is highly Professional</p>
    <p class="name">MARA ELLISON</p>
    <p class="creds">BA (Psych) BSc (Hons) Psych MBPS</p>
    <p class="lines">Mobile: 0412 555 018<br>E-mail: m.ellison@larkmail.net</p>
  </div>

  <footer class="site-footer">
    <p class="copyright">@Copyright Larkfield 2013 . Alright reserve</p>
    <div class="social"><span></span><span></span></div>
    <p class="web">www.<em>larkfieldadvisory</em>.com.au</p>
  </footer>
</div>
</body>
</html>
```